BOLD & MINIMALIST DESIGN NEEDED

We want a very bold but minimalistic business card design that is impactful and utilizes both sides of the business card. Our current logo is included for your use.

We want bold fonts and good use of negative space. We don't want the logo to overpower the design.

Target Market(s)

Professionals who are building new commercial buildings.

Industry/Entity Type

Construction

Contact Information for Business Card

Name, Title, email, office phone, cell phone, website

Font styles to use
Serif
Sans Serif

Requirements
Must have
• Bold design!

```html
<!DOCTYPE html>
<html lang="en">
<head>
<meta charset="utf-8">
<title>Ridgeline Design + Build — Business Card</title>
<link rel="stylesheet" href="https://fonts.googleapis.com/css2?family=Montserrat:wght@400;500;700;800;900&display=swap">
<style>
  :root {
    --green: #7dc242;
    --green-light: #93cf5c;
    --black: #111111;
    --ink: #222222;
    --white: #ffffff;
    --backdrop: #e9eaea;
  }
  * { box-sizing: border-box; margin: 0; padding: 0; }
  html, body {
    width: 1200px; height: 900px; overflow: hidden;
    background: var(--backdrop);
    font-family: "Montserrat", sans-serif;
  }
  .sheet {
    position: relative; width: 1200px; height: 900px;
  }
  .card {
    position: absolute; width: 630px; height: 360px;
    border-radius: 22px; overflow: hidden;
    box-shadow: 0 10px 28px rgba(0,0,0,0.18);
  }
  /* Back side */
  .card-back {
    left: 170px; top: 60px;
    background: linear-gradient(120deg, var(--green) 0%, var(--green-light) 55%, var(--green) 100%);
    display: flex; align-items: center; justify-content: center;
  }
  .back-wordmark {
    display: flex; align-items: center; gap: 18px;
    color: var(--white); font-weight: 800; font-size: 54px; letter-spacing: 2px;
  }
  .back-wordmark .mark-square {
    width: 44px; height: 44px; background: var(--white);
  }
  /* Front side */
  .card-front {
    left: 400px; top: 470px;
    background: var(--white);
  }
  .front-swoosh { position: absolute; left: 0; bottom: 0; width: 630px; height: 150px; }
  .brand {
    position: absolute; left: 40px; top: 120px; width: 270px;
    text-align: center;
  }
  .brand-name {
    font-weight: 800; font-size: 38px; color: var(--black); letter-spacing: 1px; line-height: 1;
  }
  .brand-tagline {
    margin-top: 8px; font-weight: 800; font-size: 14px; letter-spacing: 6px; color: var(--black);
  }
  .divider {
    position: absolute; left: 330px; top: 60px; width: 2px; height: 180px;
    background: var(--green);
  }
  .contact {
    position: absolute; left: 352px; top: 40px; width: 260px;
  }
  .person-name {
    font-weight: 800; font-size: 30px; color: var(--green); letter-spacing: 1px; line-height: 1;
  }
  .person-title {
    margin-top: 4px; font-weight: 500; font-size: 13px; color: var(--ink); letter-spacing: 1px;
  }
  .address {
    margin-top: 12px; font-size: 13px; line-height: 1.45; color: var(--ink);
  }
  .contact-list { list-style: none; margin-top: 10px; }
  .contact-list li {
    display: flex; align-items: center; gap: 8px;
    font-size: 13px; line-height: 1.55; color: var(--ink);
  }
  .contact-list svg { width: 13px; height: 13px; fill: var(--green); flex: none; }
</style>
</head>
<body>
<main class="sheet">

  <section class="card card-back" aria-label="Card back">
    <div class="back-wordmark"><span class="mark-square"></span>RIDGELINE</div>
  </section>

  <section class="card card-front" aria-label="Card front">
    <svg class="front-swoosh" viewBox="0 0 630 150" preserveAspectRatio="none" aria-hidden="true">
      <path d="M0 110 C 200 150, 420 40, 630 20 L630 150 L0 150 Z" fill="var(--black)"/>
      <path d="M0 118 C 200 158, 420 52, 630 32 L630 150 L0 150 Z" fill="var(--white)"/>
      <path d="M0 126 C 200 162, 420 62, 630 40 L630 150 L0 150 Z" fill="var(--green)"/>
    </svg>

    <div class="brand">
      <div class="brand-name">RIDGELINE</div>
      <div class="brand-tagline">DESIGN + BUILD</div>
    </div>

    <div class="divider"></div>

    <div class="contact">
      <h1 class="person-name">ARJUN MEHTA</h1>
      <p class="person-title">OWNER-CEO</p>
      <p class="address">Your address, City<br>State, Zip 1234</p>
      <ul class="contact-list">
        <li><svg viewBox="0 0 24 24"><path d="M6.6 10.8a15 15 0 0 0 6.6 6.6l2.2-2.2a1 1 0 0 1 1-.25 11.4 11.4 0 0 0 3.6.57 1 1 0 0 1 1 1V20a1 1 0 0 1-1 1A17 17 0 0 1 3 4a1 1 0 0 1 1-1h3.5a1 1 0 0 1 1 1c0 1.25.2 2.45.57 3.57a1 1 0 0 1-.25 1z"/></svg>123 456 789</li>
        <li><svg viewBox="0 0 24 24"><path d="M7 1h10a2 2 0 0 1 2 2v18a2 2 0 0 1-2 2H7a2 2 0 0 1-2-2V3a2 2 0 0 1 2-2zm0 3v14h10V4zm5 15.5a1 1 0 1 0 0 2 1 1 0 0 0 0-2z"/></svg>123 456 789</li>
        <li><svg viewBox="0 0 24 24"><path d="M2 5h20v14H2zm2 2v.5l8 5 8-5V7zm0 2.8V17h16V9.8l-8 5z"/></svg>info@yourmail.com</li>
        <li><svg viewBox="0 0 24 24"><path d="M12 2a10 10 0 1 0 0 20 10 10 0 0 0 0-20zm-1 17.9A8 8 0 0 1 4 12l5 5v1a2 2 0 0 0 2 2zm6.9-2.5A2 2 0 0 0 16 16h-1v-3a1 1 0 0 0-1-1H8v-2h2a1 1 0 0 0 1-1V7h2a2 2 0 0 0 2-2v-.4a8 8 0 0 1 2.9 12.8z"/></svg>www.yourwebsite.com</li>
      </ul>
    </div>
  </section>

</main>
</body>
</html>
```